Zielgruppe
Wir sind Sydneys führender Brick and Stone Restorator.
Aufgabenstellung
Unsere neue webseite geht in ein paar tagen online und wir möchten gerne passenden zur neuen Webseite ein corporate Flyer, letztendlich soll es ein Print Version von unserer neuen Webseite sein. Sprich die wichtigsten Informationen der Webseite soll in dem Flyer enthalten sein. Letztendlich möchte ich designer keine großen einschränkungen geben, weil das ist euer job kreativ sein ;), aber der flyer sollte evtl. so aufgebaut sein das am Ende die leute entweder uns anrufen oder doch auf unsere neue Webseite gehen sprich evtl ein QR- code or what ever.
Unsere Domain ist ostravagrouting.com.au, aber damit ihr die neue Webseite schon sehen könnt müsst ihr auf ostravagrouting.com.au/ new, falls dieser Link nicht mehr funktionieren sollte, ist sie schon auf der richtigen domain hochgeladen.
Falls ihr irgendwelche Logos Bilder oder sonst was benötigt und diese nicht aus der Webseite entnehmen könnt, schickt einfach eine kurze Naricht, ich beantworte diese so schnell wie möglich ;)
der Flyer soll ein 6 pager sein!!
mit freundlichen Grüßen euer Ostrava Grouting Team

```html
<!DOCTYPE html>
<html lang="en">
<head>
<meta charset="utf-8">
<title>Ostrava Grouting – Trifold Brochure</title>
<link rel="stylesheet" href="https://fonts.googleapis.com/css2?family=Quicksand:wght@400;500&family=Poppins:wght@400;500;600&display=swap">
<style>
  :root {
    --plum: #3a2d5c;
    --plum-deep: #2f2450;
    --sand: #e4dac0;
    --sand-light: #ece3cd;
    --white: #ffffff;
    --stage: #6d6d70;
    --stage-line: #9a9a9e;
    --brick-gold: #c99a4e;
    --brick-red: #7a3f33;
    --stone-grey: #a9a7a2;
  }
  * { margin: 0; padding: 0; box-sizing: border-box; }
  html, body { width: 1119px; height: 1200px; overflow: hidden; }
  body {
    background: var(--stage);
    position: relative;
    font-family: "Poppins", sans-serif;
    color: var(--plum);
  }

  .measure { position: absolute; color: var(--stage-line); font-family: "Quicksand", sans-serif; font-size: 12px; }
  .measure-rule { position: absolute; top: 45px; left: 41px; width: 1029px; height: 1px; background: var(--stage-line); }
  .measure-width { top: 28px; width: 343px; text-align: center; }
  .measure-height { left: 14px; top: 270px; transform: rotate(-90deg); }

  .spread { position: absolute; left: 41px; width: 1029px; height: 516px; overflow: hidden; }
  .spread-outside { top: 50px; }
  .spread-inside { top: 605px; }
  .spread svg.spread-art { position: absolute; inset: 0; width: 1029px; height: 516px; }

  .abs { position: absolute; }

  /* Outside spread */
  .quote { left: 23px; top: 372px; width: 250px; font-family: "Quicksand", sans-serif; font-size: 10.4px; line-height: 16.2px; color: var(--plum); }
  .quote-mark { font-family: "Poppins", sans-serif; font-weight: 600; font-size: 30px; line-height: 20px; height: 20px; display: block; }
  .quote-close { text-align: right; margin-top: 2px; }
  .quote strong { font-family: "Poppins", sans-serif; font-weight: 600; }

  .wordmark { font-family: "Poppins", sans-serif; font-weight: 600; letter-spacing: 0.5px; display: flex; align-items: center; gap: 6px; }
  .wordmark-square { display: inline-block; background: currentColor; }
  .wordmark-contact { left: 382px; top: 268px; color: var(--white); font-size: 15px; }
  .wordmark-contact .wordmark-square { width: 9px; height: 9px; }
  .wordmark-cover { left: 686px; width: 343px; top: 462px; justify-content: center; color: var(--plum); font-size: 22px; }
  .wordmark-cover .wordmark-square { width: 13px; height: 13px; }

  .contact { left: 382px; color: var(--white); font-size: 8.6px; line-height: 12.5px; }
  .contact-intro { top: 307px; width: 280px; }
  .contact-row { display: flex; align-items: center; gap: 6px; }
  .contact-row svg { width: 11px; height: 11px; flex: none; }
  .contact-row .divider { width: 1px; height: 20px; background: var(--white); flex: none; }
  .contact-row .divider.short { height: 12px; }
  .row-address { top: 344px; }
  .row-po { top: 383px; }
  .row-phone { top: 425px; }
  .row-web { top: 454px; font-size: 12.5px; font-weight: 500; letter-spacing: 0.3px; }
  .licence { left: 565px; top: 490px; color: var(--white); font-family: "Quicksand", sans-serif; font-size: 8.5px; }

  /* Inside spread */
  .service { position: absolute; }
  .service-title { font-family: "Quicksand", sans-serif; font-weight: 500; font-size: 17px; line-height: 16px; display: flex; align-items: center; gap: 6px; }
  .service-title svg { width: 22px; height: 18px; flex: none; }
  .service-body { font-size: 7.6px; line-height: 10.5px; margin-top: 6px; text-align: justify; }
  .on-plum { color: var(--white); }
  .on-sand { color: var(--plum); }
  .align-right .service-title { justify-content: flex-end; text-align: left; }
  .align-right .service-body { text-align: right; white-space: nowrap; }
</style>
</head>
<body>

<div class="measure-rule"></div>
<div class="measure measure-width" style="left:41px">14 cm</div>
<div class="measure measure-width" style="left:384px">14 cm</div>
<div class="measure measure-width" style="left:727px">14 cm</div>
<div class="measure measure-height">21 cm</div>

<!-- Outside: back panel, contact panel, cover -->
<section class="spread spread-outside">
  <svg class="spread-art" viewBox="0 0 1029 516">
    <rect x="0" y="0" width="343" height="516" fill="var(--sand)"/>
    <rect x="343" y="0" width="343" height="516" fill="var(--plum)"/>
    <rect x="686" y="0" width="343" height="516" fill="var(--white)"/>

    <polygon points="86,0 343,0 343,129" fill="var(--sand-light)"/>
    <polygon role="img" aria-label="Photo: close-up of a golden sandstone brick wall with a glass block window" points="0,0 86,0 343,129 343,453 0,289" fill="var(--brick-gold)"/>
    <polygon points="86,0 100,0 343,122 343,129" fill="var(--plum)"/>
    <polygon points="0,283 343,447 343,462 0,297" fill="var(--plum)"/>

    <polygon role="img" aria-label="Photo: rough-faced grey stone block wall" points="343,0 686,0 686,298 343,123" fill="var(--stone-grey)"/>
    <polygon points="343,123 686,298 686,306 343,131" fill="var(--sand)"/>
    <polygon points="343,462 343,470 436,516 452,516" fill="var(--sand)"/>

    <polygon points="686,298 865,386 1029,307 1029,317 865,396 686,308" fill="var(--sand)"/>
    <polygon role="img" aria-label="Photo: three-storey red brick heritage building with arched white windows" points="686,0 1029,0 1029,307 865,386 686,298" fill="var(--brick-red)"/>
  </svg>

  <div class="abs quote">
    <span class="quote-mark">&ldquo;</span>
    With over 20 years<br>
    of professional experience<br>
    and continuing development,<br>
    <strong>Ostrava Grouting</strong> have restored and<br>
    renovated the brick work of homes, churches,<br>
    town halls and heritage buildings all over NSW.
    <span class="quote-mark quote-close">&rdquo;</span>
  </div>

  <div class="abs wordmark wordmark-contact"><span class="wordmark-square"></span>OSTRAVA GROUTING</div>

  <p class="abs contact contact-intro">Ostrava Grouting are located in Sydney’s Eastern Suburbs and cater to all areas.</p>

  <div class="abs contact contact-row row-address">
    <svg viewBox="0 0 12 12"><path d="M6 0.5a4 4 0 0 0-4 4c0 3 4 7 4 7s4-4 4-7a4 4 0 0 0-4-4zm0 5.6a1.6 1.6 0 1 1 0-3.2 1.6 1.6 0 0 1 0 3.2z" fill="#fff"/></svg>
    <span class="divider"></span>
    <span>12 / 4-6 Harbour Lane, Eastgate,<br>NSW, 2020, Australia</span>
  </div>
  <div class="abs contact contact-row row-po">
    <svg viewBox="0 0 12 12"><path d="M6 1 0.5 6h1.5v5h3V8h2v3h3V6h1.5z" fill="#fff"/></svg>
    <span class="divider"></span>
    <span>PO Box 2873, Coralbay,<br>NSW 2036</span>
  </div>
  <div class="abs contact contact-row row-phone">
    <svg viewBox="0 0 12 12"><path d="M2.5 0.8 4.6 3 3.6 4.4c.7 1.6 2 2.9 3.9 3.9L9 7.4l2.2 2.1-1.3 1.7C5.5 11 1 6.5.8 2.1z" fill="#fff"/></svg>
    <span class="divider short"></span>
    <span>Office phone: 0400 555 017</span>
  </div>
  <div class="abs contact contact-row row-web">
    <svg viewBox="0 0 12 12" fill="none" stroke="#fff" stroke-width="0.9"><circle cx="6" cy="6" r="5"/><ellipse cx="6" cy="6" rx="2.2" ry="5"/><path d="M1 6h10M1.8 3.5h8.4M1.8 8.5h8.4"/></svg>
    <span class="divider short"></span>
    <span>www.ostravagrouting.com.au</span>
  </div>
  <p class="licence abs">Licence no: 481706B</p>

  <div class="abs wordmark wordmark-cover"><span class="wordmark-square"></span>OSTRAVA GROUTING</div>
</section>

<!-- Inside: services -->
<section class="spread spread-inside">
  <svg class="spread-art" viewBox="0 0 1029 516">
    <rect x="0" y="0" width="343" height="516" fill="var(--plum)"/>
    <rect x="343" y="0" width="343" height="516" fill="var(--sand)"/>
    <rect x="686" y="0" width="343" height="516" fill="var(--plum)"/>

    <polygon role="img" aria-label="Photo: dark brown brick apartment block with window boxes" points="0,0 343,0 343,272 117,165 0,232" fill="#6d4a48"/>
    <polygon points="0,232 117,165 343,272 343,282 117,175 0,242" fill="var(--sand)"/>

    <polygon role="img" aria-label="Photo: cream brick inter-war building corner with white sash windows" points="343,0 686,0 686,154 343,272" fill="#b99a6c"/>
    <polygon role="img" aria-label="Photo: rounded red brick heritage building under a cloudy sky" points="686,0 1029,0 1029,236 686,181" fill="#94503c"/>
    <polygon points="686,181 1029,236 1029,246 686,191" fill="var(--sand)"/>
    <polygon points="343,266 843,0 862,0 343,276" fill="var(--plum)"/>
  </svg>

  <!-- Panel A -->
  <div class="service on-plum" style="left:28px; top:226px; width:290px;">
    <h2 class="service-title">
      <svg viewBox="0 0 22 18" fill="none" stroke="#fff" stroke-width="1.3"><path d="M2 11l8-6 10 4-8 6z M2 11v3l10 4v-3 M12 18l8-6v-3"/></svg>
      <span>Brick &amp; Stone<br>Repointing</span>
    </h2>
    <p class="service-body">Repointing is the process of renewing the mortar between the bricks. Weather, age &amp; decay, cause the mortar to erode leaving voids in the brick facade. Water can then enter creating issues of dampness etc. We use our own factory made Ostrava Grouting Mortar.</p>
  </div>
  <div class="service on-plum" style="left:28px; top:330px; width:290px;">
    <h2 class="service-title">
      <svg viewBox="0 0 22 18" fill="none" stroke="#fff" stroke-width="1.5"><rect x="1" y="5" width="20" height="8"/><path d="M1 9h20M8 5v4M14 9v4"/></svg>
      <span>Tuckpointing</span>
    </h2>
    <p class="service-body">Tuckpointing is the process of creating contrasting lines against the background of bricks and brick coloured mortar. After repointing and repairs are completed, with attention to detail, a thin white line is applied to create the appearance of very fine mortar joints. Red or black tuck can also be used.</p>
  </div>
  <div class="service on-plum" style="left:28px; top:424px; width:290px;">
    <h2 class="service-title">
      <svg viewBox="0 0 22 18"><path d="M2 16 9 8l5 5-7 4z" fill="#fff"/><path d="M12 9l6-7 2 2-6 7" fill="#fff"/></svg>
      <span>Restoring Brick and Stone</span>
    </h2>
    <p class="service-body">Restoration involves a variety of processes specific to individual needs. These may include removing &amp; replacing fretted, damaged or un-sightly bricks, repairing cracks &amp; settlement cracks, if necessary re-building sections, and high pressure cleaning. Paired with repointing, these processes can ensure aesthetic and structural integrity.</p>
  </div>

  <!-- Panel B -->
  <div class="service on-sand align-right" style="left:362px; top:224px; width:306px;">
    <h2 class="service-title">
      <svg viewBox="0 0 22 18" fill="none" stroke="var(--plum)" stroke-width="1.3"><path d="M3 17V8a8 7 0 0 1 16 0v9z M3 11h16M11 2v15"/></svg>
      <span>Lintel and Arch Bar<br>Replacement</span>
    </h2>
    <p class="service-body">Lintels or arch bars (for curved windows) are structural<br>horizontal blocks that span the space or opening between two<br>vertical supports. They are found over doors, windows, fireplaces<br>and some archways. We use lintels &amp; arch bars that are made from Hot<br>Dipped Galvanised stainless steel (HD Gal) or concrete.</p>
  </div>
  <div class="service on-sand" style="left:362px; top:329px; width:306px;">
    <h2 class="service-title">
      <svg viewBox="0 0 22 18"><g fill="var(--plum)"><rect x="1" y="6" width="8" height="3"/><rect x="10" y="6" width="5" height="3"/><rect x="1" y="10" width="4" height="3"/><rect x="6" y="10" width="8" height="3"/><rect x="1" y="14" width="8" height="3"/><rect x="10" y="14" width="8" height="3"/></g><path d="M14 4l3 3 5-6" fill="none" stroke="var(--plum)" stroke-width="1.6"/></svg>
      <span>Remedial Wall Tie Replacement<br>&amp; Installation</span>
    </h2>
    <p class="service-body">Wall ties are a built-in tie system to secure the facade wall of a building to it’s structural frame, and is an alternative to rebuilding walls. Replacing / installing remedial ties will strengthen and stabilise your building. Ostrava Grouting is an Approved Installer of Helixa Remedial Wall Ties.</p>
  </div>
  <div class="service on-sand" style="left:362px; top:424px; width:306px;">
    <h2 class="service-title">
      <svg viewBox="0 0 22 18"><rect x="1" y="8" width="18" height="9" fill="var(--plum)"/><path d="M5 8V3h10v5" fill="none" stroke="var(--plum)" stroke-width="1.5"/></svg>
      <span>Damp Proof Course &amp; Flashing<br>Replacement &amp; Installation</span>
    </h2>
    <p class="service-body">DPC and Flashing are both used as a barrier to prevent moisture from moving into buildings and structures. DPC and Flashing are built into external walls and made from an impervious material. Sometimes cleaning the cavity is required to access DPC and prevent moisture build-up.</p>
  </div>

  <!-- Panel C -->
  <div class="service on-plum" style="left:704px; top:240px; width:306px;">
    <h2 class="service-title">
      <svg viewBox="0 0 22 18" fill="none" stroke="#fff" stroke-width="1.2"><rect x="1" y="9" width="9" height="8"/><path d="M10 11h5v4h-5 M15 6V1h3v5"/></svg>
      <span>Ventilation<br>Replacement &amp; Installation</span>
    </h2>
    <p class="service-body">Repointing is the process of renewing the mortar between the bricks. Weather, age &amp; decay, cause the mortar to erode leaving voids in the brick facade. Water can then enter creating issues of dampness etc. We use our own factory made Ostrava Grouting Mortar.</p>
  </div>
  <div class="service on-plum" style="left:700px; top:335px; width:310px;">
    <h2 class="service-title">
      <svg viewBox="0 0 22 18" fill="none" stroke="#fff" stroke-width="1.3"><path d="M7 2c-3 5-5 7-5 10a5 5 0 0 0 10 0c0-3-2-5-5-10z M16 1c-2 3-3 4-3 6a3 3 0 0 0 6 0c0-2-1-3-3-6z"/></svg>
      <span>Water Repellant</span>
    </h2>
    <p class="service-body">Norvane Water Repellant is a clear impregnating water repellant that penetrates and chemically reacts with the surface, preventing deterioration by keeping water out, and allowing moisture to escape. The water repellant is applied after repointing for optimum moisture prevention.</p>
  </div>
  <div class="service on-plum" style="left:700px; top:435px; width:310px;">
    <h2 class="service-title">
      <svg viewBox="0 0 22 18" fill="none" stroke="#fff" stroke-width="1.4"><path d="M3 1v17M17 1v17M3 4h14M3 9h14M3 14h14M3 4l14 5M3 9l14 5"/></svg>
      <span>Scaffolding Services</span>
    </h2>
    <p class="service-body">Ostrava Grouting can supply and erect our own scaffolding. Our trained staff provide safety compliant platforms for our team to complete works on multi storey, hard to reach or awkward positioned buildings. This allows us to work independently and cost effectively.</p>
  </div>
</section>

</body>
</html>
```